Seeking for catalogue design -for Event Mgmt company

Need to be creative and striking and images to be more enhanced.
The items in the catalogue have to be layout well and easy to read.
Cover and background of catalogue needs to be striking but not overpowering the items.
Catologue needs to be able to put up on website and able to read on mobile.
Font used must be easily readable and not too small.

Target Market(s)

Business and Public Sectors

Industry/Entity Type

Event Planning

Colors

Designer to choose colors to be used in the design.

Requirements
Must have
• Not too many colors but must be creative
Nice to have
• See that the images of items in catalogue have better layout
Should not have
• Not to be so messy

```html
<!DOCTYPE html>
<html lang="en">
<head>
<meta charset="utf-8">
<title>Lanterna Events – Stall Pricing Catalogue</title>
<link rel="stylesheet" href="https://fonts.googleapis.com/css2?family=Montserrat:wght@600;700;800&family=League+Spartan:wght@700;800&family=Poppins:wght@400;600;700&family=Alfa+Slab+One&family=Roboto+Slab:wght@400&display=swap">
<style>
  :root{
    --yellow:#f5c453;
    --yellow-soft:#f8cd62;
    --yellow-deep:#eebb48;
    --ornament:rgba(31,34,54,.07);
    --ink:#0d0d0d;
    --white:#ffffff;
    --slate:#9b9ca7;
    --red:#f6555a;
    --bar:#4b3a17;
  }
  *{margin:0;padding:0;box-sizing:border-box}
  html,body{width:1200px;height:852px;overflow:hidden;background:var(--yellow)}
  .spread{position:relative;width:1200px;height:852px;overflow:hidden;
    background:linear-gradient(90deg,transparent 0 303px,var(--yellow-deep) 303px 600px,transparent 600px 908px,var(--yellow-deep) 908px 1200px);
    font-family:"Poppins",sans-serif;color:var(--ink)}
  .band{position:absolute;background:var(--yellow-soft);opacity:.55;border-radius:40px}
  .ornament{position:absolute;background:var(--ornament);border-radius:6px}
  .divider{position:absolute;left:599px;top:0;width:3px;height:852px;background:var(--ink)}

  .brand{position:absolute;left:324px;top:92px;width:276px;height:92px;background:var(--slate);
    display:flex;flex-direction:column;align-items:center;justify-content:center;color:var(--white);
    font-family:"Montserrat",sans-serif;font-weight:700}
  .brand-name{font-size:34px;letter-spacing:1px;line-height:1}
  .brand-sub{font-size:10.5px;letter-spacing:1.6px;margin-top:6px}

  .cover-title{position:absolute;left:40px;top:336px;width:520px;text-align:center;white-space:nowrap;
    font-family:"Montserrat",sans-serif;font-weight:800;font-size:70px;letter-spacing:3px;line-height:1}
  .cover-sub{position:absolute;left:40px;top:434px;width:520px;text-align:center;white-space:nowrap;
    font-family:"Montserrat",sans-serif;font-weight:600;font-size:34px;letter-spacing:12px;padding-left:12px;line-height:1}

  .page-no{position:absolute;background:var(--white);font-weight:400;font-size:19px;line-height:32px;padding-left:1px}
  .page-no.left{left:36px;top:818px;width:82px}
  .page-no.right{left:1117px;top:822px;width:83px;height:30px;line-height:34px}

  .item{position:absolute;left:630px;width:560px;height:230px}
  .item-photo{position:absolute;left:0;top:0;width:130px;height:170px;background:var(--white);padding:3px}
  .item-photo .inner{width:100%;height:100%;border:2px solid var(--yellow);padding:3px;background:var(--white)}
  .item-photo .fill{width:100%;height:100%}
  .item-no{position:absolute;left:144px;top:-4px;font-family:"Montserrat",sans-serif;font-weight:800;
    font-size:66px;color:var(--white);line-height:1;letter-spacing:-2px}
  .item-kind{position:absolute;left:267px;top:2px;font-weight:700;font-size:23.5px;line-height:1.1;white-space:nowrap}
  .item-title{position:absolute;left:144px;top:70px;font-family:"League Spartan",sans-serif;font-weight:800;
    font-size:34px;line-height:.9;letter-spacing:-1px;white-space:nowrap}
  .item-need{position:absolute;left:144px;top:144px;font-family:"Roboto Slab",serif;font-size:10.5px;letter-spacing:1.5px;white-space:nowrap}
  .item-need b{font-weight:400;color:var(--white)}
  .item-rule{position:absolute;left:300px;top:66px;width:3px;height:96px;background:var(--white)}
  .item-rule::after{content:"";position:absolute;left:3px;top:42px;border:4px solid transparent;border-left-color:var(--white)}
  .item-price{position:absolute;left:325px;top:58px;font-family:"Alfa Slab One",serif;font-size:34px;line-height:1}
  .item-terms{position:absolute;left:423px;top:64px;font-size:11.5px;line-height:1.2;white-space:nowrap}
  .item-terms strong{font-weight:700;display:block}
  .item-size{position:absolute;left:324px;top:120px;width:119px;height:38px;background:var(--red);
    font-family:"League Spartan",sans-serif;font-weight:700;font-size:15px;line-height:40px;text-align:center;white-space:nowrap}
  .item-bar{position:absolute;left:221px;top:170px;width:71px;height:8px;background:var(--bar)}
</style>
</head>
<body>
<div class="spread">
  <div class="band" style="left:-40px;top:46px;width:640px;height:145px"></div>
  <div class="band" style="left:-40px;top:235px;width:170px;height:40px"></div>
  <div class="band" style="left:333px;top:238px;width:300px;height:40px"></div>
  <div class="band" style="left:55px;top:315px;width:560px;height:160px;border-radius:80px"></div>
  <div class="band" style="left:-40px;top:535px;width:530px;height:160px;border-radius:80px"></div>
  <div class="band" style="left:-40px;top:780px;width:640px;height:90px"></div>
  <div class="band" style="left:610px;top:235px;width:130px;height:40px"></div>
  <div class="band" style="left:940px;top:236px;width:270px;height:42px"></div>
  <div class="band" style="left:610px;top:320px;width:600px;height:200px;border-radius:90px"></div>
  <div class="band" style="left:610px;top:585px;width:470px;height:140px;border-radius:70px"></div>

  <div class="ornament" role="img" aria-label="Decorative dot pattern" style="left:87px;top:2px;width:82px;height:146px"></div>
  <div class="ornament" role="img" aria-label="Decorative wavy line" style="left:232px;top:0;width:14px;height:96px"></div>
  <div class="brand">
    <span class="brand-name">LANTERNA</span>
    <span class="brand-sub">LANTERNA EVENTS PTE LTD</span>
  </div>
  <div class="ornament" role="img" aria-label="Decorative wavy line" style="left:503px;top:238px;width:96px;height:14px"></div>

  <h1 class="cover-title">CATALOGUE</h1>
  <p class="cover-sub">STALL PRICING</p>

  <div class="ornament" role="img" aria-label="Decorative wavy line" style="left:0;top:616px;width:128px;height:14px"></div>
  <div class="ornament" role="img" aria-label="Decorative dot pattern" style="left:11px;top:693px;width:175px;height:83px"></div>
  <div class="ornament" role="img" aria-label="Decorative wavy line" style="left:418px;top:708px;width:14px;height:144px"></div>
  <div class="ornament" role="img" aria-label="Decorative dot pattern" style="left:475px;top:658px;width:85px;height:172px"></div>
  <div class="page-no left">PAGE 1</div>

  <div class="divider"></div>

  <article class="item" style="top:47px">
    <div class="item-photo"><div class="inner"><div class="fill" role="img" aria-label="Photo of the carnival ring toss game board" style="background:linear-gradient(180deg,#e8eef2 0%,#e8eef2 35%,#e4605a 45%,#1d2230 75%,#141824 100%)"></div></div></div>
    <div class="item-no">01</div>
    <div class="item-kind">CARNIVAL GAME STALL</div>
    <h2 class="item-title">carnival<br>ring toss</h2>
    <p class="item-need">REQUIRE <b>1X</b> TABLE</p>
    <div class="item-rule"></div>
    <div class="item-price">$145</div>
    <p class="item-terms"><strong>/stall (min 3 Stalls)</strong>subsequent day : $70</p>
    <div class="item-size">0.93m by 0.93m</div>
    <div class="item-bar"></div>
  </article>

  <article class="item" style="top:340px">
    <div class="item-photo"><div class="inner"><div class="fill" role="img" aria-label="Photo of the milk cans toss game board" style="background:linear-gradient(180deg,#d9e3ec 0%,#e9c35a 35%,#d9e3ec 60%,#3a3d44 80%,#dfe6ee 100%)"></div></div></div>
    <div class="item-no">02</div>
    <div class="item-kind">CARNIVAL GAME STALL</div>
    <h2 class="item-title" style="top:76px">milk<br>cans toss</h2>
    <p class="item-need" style="top:148px">REQUIRE <b>1X</b> TABLE</p>
    <div class="item-rule" style="left:294px;top:62px"></div>
    <div class="item-price" style="left:323px;top:62px">$145</div>
    <p class="item-terms" style="top:68px"><strong>/stall (min 3 Stalls)</strong>subsequent day : $70</p>
    <div class="item-size">0.93m by 0.93m</div>
    <div class="item-bar" style="left:223px"></div>
  </article>

  <article class="item" style="top:621px">
    <div class="item-photo"><div class="inner"><div class="fill" role="img" aria-label="Photo of the match the colour game board" style="background:linear-gradient(180deg,#2a2a2e 0%,#6a4a8a 25%,#2a2a2e 45%,#c9483f 65%,#3f8a4a 80%,#1f1f24 100%)"></div></div></div>
    <div class="item-no">03</div>
    <div class="item-kind">CARNIVAL GAME STALL</div>
    <h2 class="item-title" style="top:76px">match<br>the colour</h2>
    <p class="item-need" style="top:147px">REQUIRE <b>1X</b> TABLE</p>
    <div class="item-rule" style="top:64px"></div>
    <div class="item-price" style="top:60px">$145</div>
    <p class="item-terms" style="top:66px"><strong>/stall (min 3 Stalls)</strong>subsequent day : $70</p>
    <div class="item-size" style="top:121px">0.93m by 0.93m</div>
    <div class="item-bar" style="top:174px"></div>
  </article>

  <div class="page-no right">PAGE 2</div>
</div>
</body>
</html>
```